International Clinical Software Company needs a new business card design

We are looking for a new business card design for our company that has recently expanded into the UK market, making us a multinational company.
After having rebranded our website and produced a new style guide, we are looking for a business card that is creative and attention grabbing, while being consistent with the style and colour scheme used on the new website, www.plumvora.example
We produce care management technology for the aged care market, but the main aspect we aim to communicate is the human element of our software, and the way it assists in providing better care for aged people, and stronger relationships between aged people and the staff that care for them.
Our current business card is a dark green with gold text, which makes the text quite difficult to read, not very aesthetically appealing and the colour scheme looks quite dated.
We would like something fresh and modern, that can still be colourful but doesn't use large blocks of dark colour, and uses the colours within our logo.
Something tying in with the leaves that are used in our logo could work quite nicely, along with the Autumn/Fall colours of soft greens, yellows and reds (also in our existing logo). However also happy to look at fresh, completely out of the box ideas we may not have yet considered.
Target Market(s)
The people that receive this business card work in the aged card or health industry and are either corporate/management level staff or clinical (Registered Nurses, care workers etc.)
Industry/Entity Type
Health Product
Contact Information for Business Card
Company Name - BrindlewayCare
Company locations: United Kingdom, Australia, New Zealand
Staff Details:
Staff name: Derek Mallow
Staff job title: Executive Chairman
Staff email: d.mallow@plumvora.example
Office phone number: 01742 918576
Font styles to use
Other font styles liked:
- Calibri
Requirements
Must have
- Must include the BrindlewayCare brand name in it's current font
- Must include logo (3 leaves in gold circle)
- Must include Business Card Details
Nice to have
- Elements of gold
- White space
- Something autumn themed but not too cliched
Should not have
- No blue - used by a major competitor and we would like to differentiate from them
- Large blocks of dark green colour (the green that appears in our leaves on the logo on our current business card is the background colour and it is far too dark)

```html
<!DOCTYPE html>
<html lang="en">
<head>
<meta charset="utf-8">
<title>BrindlewayCare Business Card</title>
<link rel="stylesheet" href="https://fonts.googleapis.com/css2?family=Open+Sans:wght@400;600&display=swap">
<style>
  :root {
    --backdrop: #e4e4e2;
    --card: #f7f7f6;
    --gold: #a08a62;
    --gold-text: #9a8560;
    --crimson: #a0123f;
    --ink: #47474a;
    --icon: #6b6b6e;
  }
  html, body {
    margin: 0;
    padding: 0;
    width: 1105px;
    height: 1200px;
    overflow: hidden;
    background: var(--backdrop);
    font-family: "Open Sans", Calibri, sans-serif;
  }
  .card {
    position: absolute;
    left: 52px;
    top: 313px;
    width: 1000px;
    height: 574px;
    background: var(--card);
    overflow: hidden;
  }
  .gold-band {
    position: absolute;
    left: 764px;
    top: 0;
    width: 236px;
    height: 574px;
    background: var(--gold);
  }
  .emblem {
    position: absolute;
    left: 425px;
    top: 7px;
    width: 556px;
    height: 556px;
    box-sizing: border-box;
    border-radius: 50%;
    border: 7px solid var(--gold);
    background: var(--card);
    display: flex;
    align-items: center;
    justify-content: center;
  }
  .emblem-name {
    font-size: 46px;
    font-weight: 400;
    color: var(--gold-text);
  }
  .wordmark {
    position: absolute;
    left: 74px;
    top: 80px;
    margin: 0;
    font-size: 48px;
    font-weight: 400;
    color: var(--gold-text);
    line-height: 1;
  }
  .person-name {
    position: absolute;
    left: 74px;
    top: 176px;
    margin: 0;
    font-size: 35px;
    font-weight: 600;
    color: var(--gold-text);
    line-height: 1;
  }
  .person-title {
    position: absolute;
    left: 74px;
    top: 219px;
    margin: 0;
    font-size: 27px;
    font-weight: 400;
    color: var(--crimson);
    line-height: 1;
  }
  .locations {
    position: absolute;
    left: 74px;
    top: 268px;
    margin: 0;
    padding: 0;
    list-style: none;
    font-size: 26px;
    color: var(--ink);
    line-height: 35px;
  }
  .locations li {
    position: relative;
    padding-left: 24px;
  }
  .locations li::before {
    content: "";
    position: absolute;
    left: 0;
    top: 15px;
    width: 7px;
    height: 7px;
    border-radius: 50%;
    background: var(--gold);
  }
  .contacts {
    position: absolute;
    left: 72px;
    top: 389px;
    margin: 0;
    padding: 0;
    list-style: none;
    font-size: 26px;
    color: var(--ink);
    line-height: 38.5px;
  }
  .contacts li {
    display: flex;
    align-items: center;
    gap: 14px;
  }
  .contact-icon {
    width: 22px;
    height: 22px;
    fill: var(--icon);
    flex: none;
  }
</style>
</head>
<body>
  <main class="card">
    <div class="gold-band"></div>
    <div class="emblem">
      <span class="emblem-name">BrindlewayCare</span>
    </div>

    <h1 class="wordmark">BrindlewayCare</h1>
    <h2 class="person-name">Derek Mallow</h2>
    <p class="person-title">Executive Chairman</p>

    <ul class="locations">
      <li>United Kingdom</li>
      <li>Australia</li>
      <li>New Zealand</li>
    </ul>

    <ul class="contacts">
      <li>
        <svg class="contact-icon" viewBox="0 0 24 24" aria-hidden="true">
          <path d="M6.6 10.8c1.4 2.8 3.8 5.1 6.6 6.6l2.2-2.2c.3-.3.7-.4 1-.2 1.1.4 2.3.6 3.6.6.6 0 1 .4 1 1V20c0 .6-.4 1-1 1C10.6 21 3 13.4 3 4c0-.6.4-1 1-1h3.5c.6 0 1 .4 1 1 0 1.3.2 2.5.6 3.6.1.3 0 .7-.2 1z"/>
        </svg>
        <span>01742 918576</span>
      </li>
      <li>
        <svg class="contact-icon" viewBox="0 0 24 24" aria-hidden="true">
          <path d="M2 5h20v14H2z M3.5 6.5 12 13l8.5-6.5" fill="var(--icon)"/>
          <path d="M3 6l9 7 9-7" fill="none" stroke="#f7f7f6" stroke-width="1.6"/>
        </svg>
        <span>d.mallow@plumvora.example</span>
      </li>
      <li>
        <svg class="contact-icon" viewBox="0 0 24 24" aria-hidden="true">
          <circle cx="12" cy="12" r="10"/>
          <path d="M12 2v20M2 12h20M12 2c-3.5 3-3.5 17 0 20M12 2c3.5 3 3.5 17 0 20" fill="none" stroke="#f7f7f6" stroke-width="1.3"/>
        </svg>
        <span>www.plumvora.example</span>
      </li>
    </ul>
  </main>
</body>
</html>
```